New business card for a regional office of a US M&A company

We need business card for a finance company, office based in Hong Kong , our Head office is in US, our business is to Merge and acquires companies , the new office will be a regional office for the Asia Pacific region. We want to use the head office logo as attached ( but don't have to be exactly the same, can be a variation to it) as a base and then add Asia Pacific alongside the logo.
We would prefer to have be bilingual Eng + Chinese, although we don't really have Chinese company name .

Industry/Entity Type

Business

Contact Information for Business Card

Clara Jo Tsang
 

VP,
APAC M&A Operations
ORIN VANTAGE Asia Pacific Limited
 
Unit 1407, K18
18 Tai Lok Shan Road, 
Hong Kong 
 
M: +852 6038 1742
T : +852 2836 4100
F : +852 2836 4177
VOIP: 4158
 
cjtsang@orinvantage.com

Font styles to use
Serif
Sans Serif

Colors

Designer to choose colors to be used in the design.

Requirements
Must have
• APAC Office

```html
<!DOCTYPE html>
<html lang="en">
<head>
<meta charset="utf-8">
<title>Orin Vantage – APAC Business Card</title>
<link href="https://fonts.googleapis.com/css2?family=Ubuntu:wght@500;700&family=Open+Sans:wght@400;600&display=swap" rel="stylesheet">
<style>
  :root {
    --page-bg: #e4e4e6;
    --navy: #0e2840;
    --cyan: #2a9fc4;
    --card-white: #f6f6f7;
    --ink: #1f2b38;
    --icon: #2a9fc4;
  }
  * { box-sizing: border-box; margin: 0; padding: 0; }
  html, body { width: 1200px; height: 576px; overflow: hidden; }
  body { background: var(--page-bg); position: relative; font-family: "Open Sans", Arial, sans-serif; }

  .card {
    position: absolute; top: 138px; height: 294px;
    border-radius: 13px; overflow: hidden;
  }
  .card--back { left: 82px; width: 484px; background: var(--navy); }
  .card--front { left: 602px; width: 481px; background: var(--card-white); }

  .back-strip { position: absolute; left: 0; right: 0; bottom: 0; height: 6px; background: var(--cyan); }
  .back-brand {
    position: absolute; left: 0; right: 0; top: 126px; text-align: center;
    display: flex; align-items: center; justify-content: center; gap: 14px;
  }
  .brand-square { width: 28px; height: 28px; background: var(--cyan); }
  .brand-name {
    font-family: "Ubuntu", Arial, sans-serif; font-weight: 700;
    color: var(--cyan); font-size: 36px; letter-spacing: 0.5px; line-height: 1;
  }

  .front-brand { position: absolute; left: 30px; top: 45px; display: flex; align-items: center; gap: 14px; }
  .front-brand .brand-square { width: 38px; height: 38px; }
  .front-brand .brand-name { font-size: 38px; }

  .person { position: absolute; left: 27px; top: 156px; color: var(--ink); font-size: 12px; line-height: 15px; }
  .person-name { font-family: "Ubuntu", Arial, sans-serif; font-weight: 500; color: var(--cyan); font-size: 18px; line-height: 22px; margin-bottom: 3px; }
  .person-title { margin-bottom: 18px; }

  .office { position: absolute; left: 239px; top: 158px; color: var(--ink); font-size: 12px; line-height: 15.5px; }
  .office-name { font-family: "Ubuntu", Arial, sans-serif; font-weight: 700; color: var(--cyan); font-size: 13.2px; margin-bottom: 8px; }
  .office-lines { padding-left: 12px; }
  .contact-row { display: flex; align-items: center; gap: 8px; }
  .contact-row svg { width: 9px; height: 9px; flex: none; }
  .label-accent { color: var(--cyan); }
  .address { margin-top: 2px; }

  .front-footer { position: absolute; left: 0; bottom: 0; width: 481px; height: 32px; }
  .website { position: absolute; left: 248px; bottom: 9px; color: #ffffff; font-size: 12px; letter-spacing: 0.4px; }
  .website span { color: var(--cyan); }
</style>
</head>
<body>
  <section class="card card--back">
    <div class="back-brand">
      <span class="brand-name">ORIN VANTAGE</span>
    </div>
    <div class="back-strip"></div>
  </section>

  <section class="card card--front">
    <div class="front-brand">
      <span class="brand-square"></span>
      <span class="brand-name">ORIN VANTAGE</span>
    </div>

    <div class="person">
      <p class="person-name">Clara Jo Tsang</p>
      <p class="person-title">Vice President,<br>APAC M&amp;A Operations</p>
      <p class="contact-row">
        <svg viewBox="0 0 10 10"><rect x="2" y="0.5" width="6" height="9" rx="1" fill="none" stroke="var(--icon)" stroke-width="1.4"/></svg>
        +852 6038 1742
      </p>
      <p class="contact-row">
        <svg viewBox="0 0 10 10"><rect x="0.5" y="2" width="9" height="6" fill="var(--icon)"/><path d="M0.5 2 L5 5.5 L9.5 2" fill="none" stroke="#fff" stroke-width="0.9"/></svg>
        cjtsang@orinvantage.com
      </p>
    </div>

    <div class="office">
      <p class="office-name">Orin Vantage Asia Pacific Limited</p>
      <div class="office-lines">
        <p class="contact-row">
          <svg viewBox="0 0 10 10"><path d="M1 4 Q5 0 9 4 L7.5 5 L6.5 3.5 L3.5 3.5 L2.5 5 Z M2.5 6 H7.5 V9 H2.5 Z" fill="var(--icon)"/></svg>
          +852 2836 4100
        </p>
        <p class="contact-row">
          <svg viewBox="0 0 10 10"><rect x="2.5" y="0.5" width="5" height="3" fill="var(--icon)"/><rect x="0.5" y="4" width="9" height="4" fill="var(--icon)"/><rect x="2.5" y="7" width="5" height="2.5" fill="var(--icon)"/></svg>
          <span>+852 2836 4177,&nbsp; <span class="label-accent">VOIP</span>: 4158</span>
        </p>
        <p class="address">Unit 1407, K18 18, Tai Lok<br>Shan Road, Hong Kong</p>
      </div>
    </div>

    <svg class="front-footer" viewBox="0 0 481 32" preserveAspectRatio="none">
      <rect x="0" y="20" width="215" height="12" fill="var(--cyan)"/>
      <polygon points="224,0 481,0 481,32 205,32" fill="var(--navy)"/>
    </svg>
    <p class="website">www.<span>orinvantage</span>.com</p>
  </section>
</body>
</html>
```